Clear Plastic Card Design

I am looking to have a business card designed from my logo icon. I am looking to match the style of a different business card I have attached in the files.
Looking for a card that is plastic, with layers of transparency in the shape of my logo icon (also attached in the files) - not a circle like the other card. The winning design will incorporate the red icon logo on the front and back and include the charity's name, "Light for the Weary Souls" in the same or similar font, as well as an email and phone number. For now, use the email: email@lightfortheweary-mail.org and the phone number 555-382-7194.
We like how the sample business card has transparency, partial and full opacity layers and a matching color scheme. Files will need to be in vector so that our business card printing company can work with it.
UPDATE:
We've some excellent designs in, thank you everyone! I got an early review from the owner, and he requested a minor redirect to find his perfect design. He wants the design to stand out by NOT being a rectangle. Try instead a circle, square, or best yet - something that falls in the outline of the logo icon, either fully or partially. Thank you, everyone!
Light for the Weary Souls text should be incorporated as well as a phone and email.

```html
<!DOCTYPE html>
<html lang="en">
<head>
<meta charset="UTF-8">
<title>Light for the Weary Souls – Business Card</title>
<link rel="stylesheet" href="https://fonts.googleapis.com/css2?family=Arimo:wght@400;700&family=Poppins:wght@400&display=swap">
<style>
  :root {
    --page-bg: #e7e3df;
    --card-bg: rgba(246, 246, 248, 0.92);
    --card-edge: #cfcfd4;
    --red-light: #e24a4a;
    --red-dark: #a10e14;
    --text-light: #ffffff;
    --text-soft: #f3dcdc;
    --ink: #1b1b1b;
  }
  html, body {
    margin: 0;
    width: 1200px;
    height: 900px;
    overflow: hidden;
    background: var(--page-bg);
  }
  .business-card {
    position: absolute;
    left: 280px;
    top: 236px;
    width: 672px;
    height: 384px;
    border-radius: 18px;
    background: var(--card-bg);
    border: 1px solid var(--card-edge);
    box-sizing: border-box;
    overflow: hidden;
  }
  .card-shapes {
    position: absolute;
    inset: 0;
  }
  .contact-block {
    position: absolute;
    left: 29px;
    top: 124px;
    color: var(--text-light);
    font-family: "Arimo", Arial, sans-serif;
  }
  .person-name {
    margin: 0;
    font-size: 25px;
    font-weight: 700;
    letter-spacing: 0.5px;
  }
  .person-title {
    margin: 4px 0 16px;
    font-size: 16px;
    color: var(--text-soft);
  }
  .contact-line {
    display: flex;
    align-items: center;
    gap: 9px;
    font-size: 15px;
    margin-bottom: 6px;
    color: var(--text-soft);
  }
  .contact-line svg {
    width: 13px;
    height: 13px;
    flex: none;
  }
  .brand-name {
    position: absolute;
    left: 350px;
    top: 150px;
    display: flex;
    align-items: center;
    gap: 14px;
  }
  .brand-mark {
    width: 34px;
    height: 34px;
    background: var(--red-dark);
  }
  .brand-text {
    margin: 0;
    font-family: "Poppins", Arial, sans-serif;
    font-weight: 400;
    font-size: 22px;
    line-height: 1.2;
    color: var(--ink);
  }
</style>
</head>
<body>
  <div class="business-card">
    <svg class="card-shapes" width="672" height="384" viewBox="0 0 672 384">
      <defs>
        <linearGradient id="band-red" x1="0" y1="0" x2="1" y2="0">
          <stop offset="0" stop-color="var(--red-light)"/>
          <stop offset="1" stop-color="var(--red-dark)"/>
        </linearGradient>
      </defs>
      <path class="contact-band" d="M0 90 H395 Q414 90 404 106 L290 278 Q283 290 268 290 H0 Z" fill="url(#band-red)" opacity="0.95"/>
      <path class="edge-tab" d="M672 90 V290 H656 Q642 290 642 276 V104 Q642 90 656 90 Z" fill="var(--red-dark)" opacity="0.9"/>
    </svg>

    <div class="contact-block">
      <p class="person-name">DANIEL REEVE</p>
      <p class="person-title">Founder &amp; CEO</p>
      <div class="contact-line">
        <svg viewBox="0 0 24 24" fill="none" stroke="currentColor" stroke-width="2.4"><path d="M5 3h4l2 5-3 2a12 12 0 0 0 6 6l2-3 5 2v4a2 2 0 0 1-2 2A18 18 0 0 1 3 5a2 2 0 0 1 2-2z"/></svg>
        <span>555-382-7194</span>
      </div>
      <div class="contact-line">
        <svg viewBox="0 0 24 24" fill="currentColor"><path d="M2 5h20v14H2z M3 6l9 7 9-7" stroke="#b01a1f" stroke-width="1.6"/></svg>
        <span>email@lightfortheweary-mail.org</span>
      </div>
      <div class="contact-line">
        <svg viewBox="0 0 24 24" fill="none" stroke="currentColor" stroke-width="2.2"><circle cx="12" cy="12" r="9.5"/><path d="M2.5 12h19M12 2.5c3 3 3 16 0 19M12 2.5c-3 3-3 16 0 19"/></svg>
        <span>lightfortheweary.org</span>
      </div>
    </div>

    <div class="brand-name">
      <p class="brand-text">Light for the<br>Weary Souls</p>
      <div class="brand-mark"></div>
    </div>
  </div>
</body>
</html>
```